Jolly Paws Business Card Update

I have a business card which I love. I want to keep the same logo, colours, font and style. I want to upgrade the scripting and remove some elements and add others.
On the front side under Services - remove the existing wording and insert - Providing individual coaching strategies to create happy, healthy and social canine companions
Under Denise Carvell amend the current wording to read: Qualified in Dog Behavioural Training, Natural Animal Healthcare and Animal Health Science
On the reverse side to remove the web address.

```html
<!DOCTYPE html>
<html lang="en">
<head>
<meta charset="utf-8">
<title>Jolly Paws Business Card</title>
<link href="https://fonts.googleapis.com/css2?family=Arimo:wght@400;700&family=Open+Sans:wght@600&display=swap" rel="stylesheet">
<style>
  :root {
    --page: #2a2a2a;
    --blue-deep: #1f3f8f;
    --blue-mid: #1b5cab;
    --blue-bright: #0a8fd0;
    --red-deep: #6e1c1e;
    --red-bright: #c41a22;
    --cream: #ece6cf;
    --cream-light: #f6f1de;
    --text-light: #f2f2f2;
  }
  * { box-sizing: border-box; margin: 0; padding: 0; }
  html, body { width: 1200px; height: 1138px; overflow: hidden; }
  body {
    background: var(--page);
    font-family: "Arimo", Arial, sans-serif;
    position: relative;
  }
  .card {
    position: absolute;
    border-radius: 14px;
    overflow: hidden;
    box-shadow: 0 6px 12px rgba(0,0,0,0.45);
  }

  /* Front */
  .card--front {
    left: 274px; top: 186px; width: 623px; height: 376px;
    background: linear-gradient(60deg, var(--blue-deep) 0%, var(--blue-mid) 50%, var(--blue-bright) 100%);
  }
  .brand-name {
    position: absolute; left: 35px; top: 52px;
    font-family: "Open Sans", Arial, sans-serif; font-weight: 600;
    font-size: 32px; letter-spacing: 1px; color: var(--cream-light);
  }
  .brand-tagline {
    position: absolute; left: 34px; top: 92px;
    font-size: 17px; color: var(--text-light); letter-spacing: 0.3px;
  }
  .front-services { position: absolute; left: 38px; top: 184px; width: 240px; color: var(--text-light); }
  .front-services h2 { font-size: 17px; font-weight: 700; line-height: 19px; }
  .front-services p { font-size: 16px; line-height: 19px; }
  .mark-circle { position: absolute; }
  .card--front .mark-circle { left: 328px; top: 38px; width: 260px; height: 260px; }
  .band-red {
    position: absolute; left: 0; right: 0;
    background: linear-gradient(90deg, var(--red-deep) 0%, var(--red-bright) 50%, var(--red-deep) 100%);
  }
  .card--front .band-red {
    top: 323px; bottom: 0;
    display: flex; align-items: center; justify-content: center;
    font-size: 16px; color: var(--text-light);
  }

  /* Back */
  .card--back {
    left: 276px; top: 608px; width: 618px; height: 374px;
    background: linear-gradient(180deg, var(--blue-bright) 0%, #0b86c9 55%, var(--blue-mid) 100%);
  }
  .card--back .mark-circle { left: 98px; top: 54px; width: 120px; height: 120px; }
  .back-services { position: absolute; left: 262px; top: 68px; width: 268px; color: var(--text-light); }
  .back-services h2 { font-size: 19px; font-weight: 400; line-height: 22px; margin-bottom: 12px; }
  .back-services p { font-size: 16px; line-height: 19px; }
  .band-cream {
    position: absolute; left: 0; right: 0; top: 202px; height: 30px;
    background: linear-gradient(90deg, var(--cream) 0%, var(--cream-light) 50%, var(--cream) 100%);
    display: flex; align-items: center; justify-content: center;
    font-size: 16px; color: #1a1a1a;
  }
  .card--back .band-red { top: 232px; bottom: 0; text-align: center; color: var(--text-light); }
  .person-name {
    font-family: "Open Sans", Arial, sans-serif; font-weight: 600;
    font-size: 22px; margin-top: 14px; line-height: 28px;
  }
  .person-role { font-size: 16px; line-height: 21px; margin-top: 2px; }
  .contacts {
    display: flex; justify-content: center; gap: 16px;
    font-size: 18px; margin-top: 7px; line-height: 22px;
  }
  .contact { display: flex; align-items: center; gap: 6px; }
  .contact svg { width: 16px; height: 16px; }
</style>
</head>
<body>

<section class="card card--front">
  <div class="brand-name">JOLLY PAWS</div>
  <div class="brand-tagline">HAPPY DOGS, HAPPY OWNERS</div>
  <div class="front-services">
    <h2>SERVICES</h2>
    <p>Providing individual coaching strategies to create happy, healthy and social canine companions</p>
  </div>
  <svg class="mark-circle" viewBox="0 0 260 260" aria-hidden="true">
    <circle cx="130" cy="130" r="118" fill="var(--cream)" stroke="var(--red-bright)" stroke-width="20"/>
  </svg>
  <div class="band-red">Promoting communication and connection between dogs and their families</div>
</section>

<section class="card card--back">
  <svg class="mark-circle" viewBox="0 0 120 120" aria-hidden="true">
    <circle cx="60" cy="60" r="54" fill="var(--cream)" stroke="var(--red-bright)" stroke-width="10"/>
  </svg>
  <div class="back-services">
    <h2>SERVICES</h2>
    <p>Providing individual coaching strategies to create happy, healthy and social canine companions</p>
  </div>
  <div class="band-cream">Promoting communication and connection between dogs and their families</div>
  <div class="band-red">
    <div class="person-name">Denise Carvell</div>
    <div class="person-role">Qualified in Dog Behavioural Training, Natural Animal Healthcare<br>and Animal Health Science</div>
    <div class="contacts">
      <span class="contact">
        <svg viewBox="0 0 16 16" aria-hidden="true"><circle cx="8" cy="8" r="7.5" fill="var(--text-light)"/><rect x="5.5" y="3.5" width="5" height="9" rx="1" fill="none" stroke="var(--red-deep)" stroke-width="1.2"/></svg>
        0400 123 456
      </span>
      <span class="contact">
        <svg viewBox="0 0 16 16" aria-hidden="true"><circle cx="8" cy="8" r="7.5" fill="var(--text-light)"/><rect x="4" y="5" width="8" height="6" fill="none" stroke="var(--red-deep)" stroke-width="1.2"/><path d="M4 5 L8 8.5 L12 5" fill="none" stroke="var(--red-deep)" stroke-width="1.2"/></svg>
        hello@jollypawsmail.com
      </span>
    </div>
  </div>
</section>

</body>
</html>
```